Velundra Jobs portal

Velundra Jobs is a job portal connecting job seekers and companies offering part time jobs in the Mena region, starting in the UAE. We would like to see designs that use the color blue. We have attached images to give an idea what the website should look like. When a company posts a job the job seekers are not allowed to see which company has posted a job. There should also be a coinvex gateway. On the landing page we want a catching picture that we will send.

Target Market(s)

Students and promotional workers

Logo Text

Velundra Jobs

Coding

Coded - Design and coding required

Number of Pages Required

4 page

Font styles to use
Sans Serif

Colors
33a6d7
0692cd
85cae6

```html
<!DOCTYPE html>
<html lang="en">
<head>
<meta charset="utf-8">
<title>Velundra Jobs</title>
<link href="https://fonts.googleapis.com/css2?family=Open+Sans:wght@300;400;600;700&display=swap" rel="stylesheet">
<style>
  :root {
    --blue: #33a6d7;
    --blue-deep: #0692cd;
    --blue-soft: #85cae6;
    --blue-button: #0a80bf;
    --pink: #df5690;
    --text: #4f5357;
    --white: #ffffff;
  }
  * { box-sizing: border-box; margin: 0; padding: 0; }
  html, body { width: 1200px; height: 682px; overflow: hidden; }
  body {
    font-family: "Open Sans", Arial, sans-serif;
    background: var(--white);
    position: relative;
  }
  .hero-photo {
    position: absolute; inset: 0;
    background:
      linear-gradient(90deg, rgba(255,255,255,0.97) 0%, rgba(255,255,255,0.85) 35%, rgba(255,255,255,0) 70%),
      radial-gradient(ellipse 200px 260px at 950px 260px, #e9b9a3 0%, rgba(233,185,163,0) 100%),
      radial-gradient(ellipse 160px 380px at 1110px 330px, #c49a6c 0%, rgba(196,154,108,0) 100%),
      radial-gradient(ellipse 330px 260px at 540px 330px, #c9dde7 0%, rgba(201,221,231,0) 100%),
      linear-gradient(180deg, #f3f5f7 0%, #e9eef2 60%, #f4f5f7 100%);
  }
  .top-rule { position: absolute; top: 0; left: 0; right: 0; height: 3px; background: var(--blue-deep); }
  .brand { position: absolute; left: 99px; top: 13px; }
  .brand-mark {
    width: 86px; height: 110px; margin-left: 17px;
    background: linear-gradient(160deg, #3a6fb5 0%, #45c1c4 55%, #e04f8f 100%);
    border-radius: 40px 40px 24px 24px; opacity: 0.85;
  }
  .brand-name {
    margin-top: 8px; font-size: 32px; font-weight: 400;
    color: var(--blue); letter-spacing: 0.5px;
  }
  .hero { position: absolute; left: 99px; top: 232px; width: 720px; }
  .hero-title {
    font-size: 38px; font-weight: 700; line-height: 44px;
    color: var(--blue); letter-spacing: -0.3px;
  }
  .hero-text {
    margin-top: 22px; width: 610px;
    font-size: 15.5px; font-weight: 400; line-height: 26px; color: var(--text);
  }
  .join-row { position: absolute; left: 99px; top: 423px; display: flex; align-items: center; }
  .btn {
    display: inline-flex; align-items: center; gap: 8px;
    height: 41px; padding: 0 12px; border-radius: 3px;
    font-size: 12.5px; font-weight: 600; text-transform: uppercase;
    color: var(--white); text-decoration: none;
  }
  .btn-join { width: 125px; background: linear-gradient(180deg, #1392d2, var(--blue-button)); border-bottom: 2px solid #066a9f; }
  .sign-in-note { margin-left: 22px; font-size: 15px; color: #333; }
  .sign-in-mascot {
    width: 28px; height: 38px; margin-left: 10px;
    background: linear-gradient(160deg, #3a6fb5, #45c1c4 55%, #e04f8f);
    border-radius: 12px; opacity: 0.8;
  }
  .role-row { position: absolute; left: 99px; top: 489px; display: flex; gap: 13px; }
  .btn-employer { width: 114px; height: 40px; background: linear-gradient(180deg, #9bd5ec, #6fbde0); border-bottom: 2px solid #58a9cc; justify-content: center; }
  .btn-seeker { width: 115px; height: 40px; background: linear-gradient(180deg, #e86c9f, #d64584); border-bottom: 2px solid #b8336c; justify-content: center; }
  .site-footer {
    position: absolute; left: 0; right: 0; bottom: 0; height: 47px;
    background: var(--blue-deep); color: var(--white);
    display: flex; align-items: center; font-size: 13px;
  }
  .copyright { position: absolute; left: 98px; }
  .social { position: absolute; left: 513px; display: flex; gap: 28px; }
  .social span { width: 12px; height: 12px; border-radius: 50%; background: var(--white); display: block; }
  .footer-links { position: absolute; right: 100px; }
  .footer-links a { color: var(--white); text-decoration: none; }
</style>
</head>
<body>
  <div class="hero-photo" role="img" aria-label="Photo of a smiling young woman working on a laptop, looking back over her shoulder"></div>
  <div class="top-rule"></div>

  <header class="brand">
    <div class="brand-mark" role="img" aria-label="Velundra mascot illustration"></div>
    <div class="brand-name">Velundra</div>
  </header>

  <section class="hero">
    <h1 class="hero-title">Number one platform connecting people with events companies.</h1>
    <p class="hero-text">We are&nbsp; Providing part time job for students in Dubai, if you are a student and have quite free time and want to invest it gaining extra money, so you are in the right place .</p>
  </section>

  <div class="join-row">
    <a class="btn btn-join" href="#">
      <svg width="16" height="14" viewBox="0 0 16 14"><path d="M0 6 L16 0 L12 14 L8 9 Z" fill="#fff"/><path d="M8 9 L16 0 L6 8 Z" fill="#cfe8f5"/></svg>
      Join Velundra
    </a>
    <span class="sign-in-note">for our users you can sign in !</span>
    <div class="sign-in-mascot" role="img" aria-label="Small Velundra mascot illustration"></div>
  </div>

  <div class="role-row">
    <a class="btn btn-employer" href="#">
      <svg width="12" height="14" viewBox="0 0 12 14"><circle cx="6" cy="4" r="3.5" fill="#fff"/><path d="M0 14 Q0 8 6 8 Q12 8 12 14 Z" fill="#fff"/></svg>
      &nbsp;Employer
    </a>
    <a class="btn btn-seeker" href="#">
      <svg width="18" height="14" viewBox="0 0 18 14"><circle cx="9" cy="4" r="3" fill="#fff"/><circle cx="3.5" cy="5" r="2.3" fill="#fff"/><circle cx="14.5" cy="5" r="2.3" fill="#fff"/><path d="M4 14 Q4 8 9 8 Q14 8 14 14 Z" fill="#fff"/><path d="M0 12 Q0 8 3.5 8 Q5 8 5 9 L4 12 Z M18 12 Q18 8 14.5 8 Q13 8 13 9 L14 12 Z" fill="#fff"/></svg>
      Job Seeker
    </a>
  </div>

  <footer class="site-footer">
    <span class="copyright">Copyrights are reserved to Velundra 2015</span>
    <nav class="social" aria-label="Social links"><span></span><span></span><span></span><span></span><span></span></nav>
    <nav class="footer-links"><a href="#">About us</a>&nbsp; - &nbsp;<a href="#">terms and conditions</a>&nbsp; - &nbsp;<a href="#">Sitemap</a></nav>
  </footer>
</body>
</html>
```